Website for my law practice

I am a solo practitioner, who specializes in family law and estate planning in Massachusetts. I need to re-do my website, as it is outdated. I like the idea of a nontraditional law firm website. My website address is: doloresquintanalaw.com. I would like to retain my logo in the green color, as part of the new website. I have uploaded my logo below.

My hourly rate has changed from what is listed on my current website. My new hourly rate is $385.00. Please use this hourly rate when creating the website.

Good morning,

I have reviewed the designs submitted so far. I am happy that the "dq" logo in the green color is part of each of the designs submitted. I am also happy that the standard items seen in law firm websites, such as the scales of justice, etc. were not incorporated. Although the green logo is great, I do not think rest of the website has to have the same green color throughout. Additionally, I was hoping for something more creative, to make the website standout and not the stock web designs you see everyday. Please incorporate more unique images if you can. For example of what I mean, please look at this website: https://www.rosalindfenwicklaw.com

```html
<!DOCTYPE html>
<html lang="en">
<head>
<meta charset="utf-8">
<title>Dolores Quintana, Attorney at Law</title>
<link rel="stylesheet" href="https://fonts.googleapis.com/css2?family=Outfit:wght@300;400;500;600&display=swap">
<style>
:root{
  --green:#2f8a1f;
  --green-dark:#1f6b14;
  --ink:#333333;
  --muted:#555555;
  --line:#d9d9d9;
  --soft:#eef6ea;
  --footer:#ececec;
  --white:#ffffff;
}
*{box-sizing:border-box;margin:0;padding:0}
html,body{width:1200px;height:4992px;overflow:hidden}
body{font-family:"Outfit",Arial,sans-serif;color:var(--ink);background:var(--white);position:relative}
.abs{position:absolute}
.btn{position:absolute;display:flex;align-items:center;justify-content:space-between;gap:10px;border-radius:24px;font-size:15px;letter-spacing:.3px;text-decoration:none}
.btn .dot{width:26px;height:26px;border:2px solid currentColor;border-radius:50%;display:flex;align-items:center;justify-content:center}
.btn.solid{background:var(--green);color:var(--white)}
.btn.ghost{border:2px solid var(--white);color:var(--white)}

/* header */
.site-header{position:absolute;top:0;left:0;width:1200px;height:140px;background:var(--white)}
.brand{position:absolute;left:66px;top:60px;display:flex;align-items:center;gap:10px;color:var(--green);font-weight:600;font-size:13px;line-height:14px}
.brand .mark{width:44px;height:44px;border:2px solid var(--green);border-radius:50%}
.call{position:absolute;right:62px;top:24px;display:flex;align-items:center;gap:10px;font-size:14px}
.call .ring{width:34px;height:34px;border:2px solid var(--green);border-radius:50%;display:flex;align-items:center;justify-content:center}
.call b{color:var(--green);font-weight:500}
.nav{position:absolute;right:62px;top:72px;display:flex;align-items:center;gap:38px;font-size:13px}
.nav a{color:var(--ink);text-decoration:none}
.nav a.active{color:var(--green);border-bottom:2px solid var(--green);padding-bottom:6px}
.nav a.cta{background:var(--green);color:var(--white);padding:6px 20px;border-radius:16px}

/* hero */
.hero{position:absolute;top:140px;left:0;width:1200px;height:732px;background:linear-gradient(180deg,#4f8d2c 0%,#3d7a22 45%,#5f9a3a 75%,#2f6d1b 100%);color:var(--white);text-align:center}
.hero p{position:absolute;left:0;width:1200px;top:178px;font-size:23px;font-weight:300;line-height:38px}
.hero h1{position:absolute;left:0;width:1200px;top:255px;font-size:54px;font-weight:400;line-height:68px}
.hero .btn{left:511px;top:428px;width:178px;height:48px;padding:0 10px 0 22px}

/* service cards */
.card-photo{position:absolute;top:955px;width:468px;height:380px;border-radius:6px}
.card-label{position:absolute;top:1275px;width:360px;height:110px;background:var(--white);border-radius:6px;box-shadow:0 6px 24px rgba(0,0,0,.12);display:flex;align-items:center;gap:30px;padding-left:30px;font-size:26px;font-weight:500}

/* about */
.about-title{position:absolute;left:540px;top:1640px;font-size:48px;font-weight:400}
.about-sub{position:absolute;left:540px;top:1702px;font-size:18px;color:var(--green);display:flex;align-items:center;gap:12px}
.about-sub i{display:block;width:42px;height:2px;background:var(--green)}
.about-text{position:absolute;left:540px;top:1765px;width:578px;font-size:12.4px;line-height:24px;color:var(--ink)}
.about .btn{left:534px;top:1962px;width:156px;height:42px;padding:0 8px 0 20px}

/* expertise */
.section-title{position:absolute;left:0;width:1200px;text-align:center;font-size:48px;font-weight:400}
.rule{position:absolute;height:2px;background:var(--green)}
.label{position:absolute;font-size:15px;line-height:19px;color:var(--ink)}
.label.r{text-align:right}
.label.c{text-align:center;width:300px}

/* faq */
.faq-title{position:absolute;left:66px;top:3340px;font-size:48px;font-weight:400}
.faq-item{position:absolute;left:66px;width:640px;font-size:14px;border-bottom:1px dashed #8aa77f}
.faq-item .q{display:flex;gap:14px;align-items:flex-start}
.faq-item .num{color:var(--green);min-width:14px}
.faq-item .tog{margin-left:auto;width:14px;height:14px;border-radius:50%;background:var(--green);color:var(--white);font-size:12px;line-height:14px;text-align:center;flex:none}
.faq-item.open .q span{color:var(--green)}
.faq-item .a{padding:18px 0 18px 28px;font-size:12.5px;line-height:24px}
.faq-item .a b{color:var(--green);font-weight:400}

/* contact */
.contact-title{position:absolute;left:572px;top:4070px;font-size:48px;font-weight:400}
.field{position:absolute;border:1px solid var(--line);font-size:12.5px;color:var(--muted);padding:16px 20px}
.contact .btn{left:568px;top:4400px;width:134px;height:42px;padding:0 8px 0 28px}

/* footer */
.site-footer{position:absolute;left:0;top:4615px;width:1200px;height:377px;background:var(--footer)}
.foot-h{position:absolute;top:82px;font-size:14px;font-weight:500;color:var(--green)}
.foot-links{position:absolute;left:232px;top:120px;list-style:none;font-size:13px;line-height:28px}
.foot-links li{display:flex;align-items:center;gap:10px}
.foot-links li::before{content:"";width:10px;height:10px;border:2px solid var(--green);border-radius:50%}
.foot-brand{position:absolute;left:0;width:1200px;top:175px;text-align:center;color:var(--green);font-size:22px;font-weight:500;line-height:28px}
.foot-contact{position:absolute;left:834px;top:118px;font-size:11.5px;line-height:14px}
.foot-contact .row{display:flex;gap:18px;align-items:center;margin-bottom:20px}
.foot-contact .ic{width:24px;height:24px;border:1px solid var(--green);display:flex;align-items:center;justify-content:center;flex:none}
.foot-rule{position:absolute;left:68px;top:320px;width:1066px;height:1px;background:var(--green)}
.copy{position:absolute;left:0;top:338px;width:1200px;text-align:center;font-size:12.5px}
</style>
</head>
<body>

<header class="site-header">
  <div class="brand"><span class="mark"></span><span>Dolores Quintana<br>Attorney at Law</span></div>
  <div class="call">
    <span class="ring"><svg width="16" height="16" viewBox="0 0 24 24"><path d="M6 3l3 0 2 5-2 1.5c1 2.5 3 4.5 5.5 5.5L16 13l5 2v3c0 1.5-1.5 3-3 3C10 21 3 14 3 6c0-1.5 1.5-3 3-3z" fill="none" stroke="#2f8a1f" stroke-width="2"/></svg></span>
    <span><b>CALL US :</b> (978) 555-0142</span>
  </div>
  <nav class="nav">
    <a class="active" href="#">HOME</a><a href="#">FAMILY LAW</a><a href="#">ESTATE PLANNING</a><a href="#">ABOUT</a><a href="#">LOCATION</a><a href="#">FAQ</a><a class="cta" href="#">CONTACT</a>
  </nav>
</header>

<section class="hero" role="img" aria-label="Meadow of white wildflowers in green grass">
  <p>Dolores Quintana is a Solo Practitioner<br>focusing her practice on matters pertaining to</p>
  <h1>FAMILY LAW AND<br>ESTATE PLANNING.</h1>
  <a class="btn ghost" href="#">CONTACT US <span class="dot"><svg width="12" height="12" viewBox="0 0 12 12"><path d="M2 6h8M7 3l3 3-3 3" stroke="#fff" stroke-width="1.6" fill="none"/></svg></span></a>
</section>

<section class="services">
  <div class="card-photo" style="left:112px;background:linear-gradient(135deg,#d9b58a,#b88762 55%,#e8cfa8)" role="img" aria-label="Smiling young family with a baby"></div>
  <div class="card-label" style="left:165px">
    <svg width="84" height="80" viewBox="0 0 84 80" fill="none" stroke="#2f8a1f" stroke-width="3"><circle cx="30" cy="40" r="10"/><circle cx="56" cy="40" r="10"/><path d="M12 76c0-12 8-20 18-20s18 8 18 20M38 76c0-12 8-20 18-20s18 8 18 20"/><path d="M42 6v22M28 12h28"/></svg>
    <span>Family Law</span>
  </div>
  <div class="card-photo" style="left:628px;background:linear-gradient(135deg,#6b4a2f,#8d6a48 45%,#d8d2c6 80%)" role="img" aria-label="Wooden gavel resting beside a contract document"></div>
  <div class="card-label" style="left:680px">
    <svg width="80" height="84" viewBox="0 0 80 84" fill="none" stroke="#2f8a1f" stroke-width="3"><rect x="6" y="6" width="46" height="70" rx="4"/><path d="M16 26h26M16 36h26M16 46h18"/><rect x="46" y="48" width="26" height="26"/><path d="M52 61h14M59 54v14"/></svg>
    <span>Estate planning</span>
  </div>
</section>

<section class="about">
  <svg class="abs" style="left:0;top:1480px" width="460" height="620" viewBox="0 0 460 620">
    <path d="M0 70C60 20 140 10 230 20c120 15 200 80 215 200 12 110-40 220-120 300C250 595 140 620 0 610" fill="none" stroke="#2f8a1f" stroke-width="2.5"/>
    <path d="M0 80C60 40 140 28 225 38c105 14 180 75 192 185 10 100-36 200-106 270C245 555 140 585 0 585Z" fill="#9a9a9a"/>
  </svg>
  <div class="abs" style="left:0;top:1518px;width:420px;height:565px" role="img" aria-label="Black and white portrait of the attorney"></div>
  <h2 class="about-title">ABOUT ME</h2>
  <div class="about-sub">Who Am I <i></i></div>
  <p class="about-text">Dolores is a graduate of Eastbridge University in Boston, Massachusetts. She received her Bachelors of Science degree in Criminal Justice and a minor in Political Science in 1993. While attending Eastbridge, Dolores was a Whitford Merit Scholar, graduating from the University Magna Cum Laude. Dolores obtained her Juris Doctor from Harborview University Law School in Boston, Massachusetts in 1999. During her law school career, she interned at the Office of Coastal Resources in Boston, Massachusetts.</p>
  <a class="btn solid" href="#">KNOW MORE <span class="dot"><svg width="12" height="12" viewBox="0 0 12 12"><path d="M2 6h8M7 3l3 3-3 3" stroke="#fff" stroke-width="1.6" fill="none"/></svg></span></a>
</section>

<section class="expertise">
  <h2 class="section-title" style="top:2220px">AREAS OF EXPERTISE</h2>
  <div class="rule" style="left:572px;top:2300px;width:56px"></div>
  <svg class="abs" style="left:0;top:0" width="1200" height="3200" viewBox="0 0 1200 3200">
    <circle cx="601" cy="2759" r="228" fill="none" stroke="#eeeeee" stroke-width="2"/>
    <circle cx="601" cy="2759" r="210" fill="#ffffff" stroke="#f0f0f0" stroke-width="14"/>
    <g stroke="#bfd7b6" stroke-width="1.5">
      <line x1="601" y1="2531" x2="601" y2="2495"/><line x1="715" y1="2562" x2="733" y2="2530"/>
      <line x1="798" y1="2645" x2="830" y2="2627"/><line x1="829" y1="2759" x2="865" y2="2759"/>
      <line x1="798" y1="2873" x2="830" y2="2891"/><line x1="715" y1="2956" x2="733" y2="2988"/>
      <line x1="601" y1="2987" x2="601" y2="3023"/><line x1="487" y1="2956" x2="469" y2="2988"/>
      <line x1="404" y1="2873" x2="372" y2="2891"/><line x1="373" y1="2759" x2="337" y2="2759"/>
      <line x1="404" y1="2645" x2="372" y2="2627"/><line x1="487" y1="2562" x2="469" y2="2530"/>
    </g>
    <g fill="#2f8a1f">
      <circle cx="601" cy="2531" r="3.5"/><circle cx="715" cy="2562" r="3.5"/><circle cx="798" cy="2645" r="3.5"/>
      <circle cx="829" cy="2759" r="3.5"/><circle cx="798" cy="2873" r="3.5"/><circle cx="715" cy="2956" r="3.5"/>
      <circle cx="601" cy="2987" r="3.5"/><circle cx="487" cy="2956" r="3.5"/><circle cx="404" cy="2873" r="3.5"/>
      <circle cx="373" cy="2759" r="3.5"/><circle cx="404" cy="2645" r="3.5"/><circle cx="487" cy="2562" r="3.5"/>
    </g>
    <defs>
      <g id="node">
        <circle r="42" fill="#eef6ea" stroke="#ffffff" stroke-width="6"/>
        <rect x="-14" y="-18" width="28" height="36" rx="2" fill="none" stroke="#2f8a1f" stroke-width="2"/>
        <path d="M-8 -8h16M-8 0h16M-8 8h10" stroke="#2f8a1f" stroke-width="2"/>
      </g>
    </defs>
    <use href="#node" x="601" y="2453"/><use href="#node" x="754" y="2494"/><use href="#node" x="866" y="2606"/>
    <use href="#node" x="907" y="2759"/><use href="#node" x="866" y="2912"/><use href="#node" x="754" y="3024"/>
    <use href="#node" x="601" y="3065"/><use href="#node" x="448" y="3024"/><use href="#node" x="336" y="2912"/>
    <use href="#node" x="295" y="2759"/><use href="#node" x="336" y="2606"/><use href="#node" x="448" y="2494"/>
  </svg>
  <div class="abs" style="left:421px;top:2579px;width:360px;height:360px;border-radius:50%;background:linear-gradient(135deg,#5a5a5a 0%,#9a8a78 35%,#e6e6e6 60%,#f4f4f4 100%)" role="img" aria-label="Gavel and pen resting on an agreement document"></div>

  <div class="label c" style="left:451px;top:2354px">Pre and Post<br>Nuptial Agreements</div>
  <div class="label" style="left:806px;top:2476px">Divorce</div>
  <div class="label" style="left:913px;top:2586px">Post - Divorce</div>
  <div class="label" style="left:958px;top:2745px">Will</div>
  <div class="label" style="left:931px;top:2900px">Memorandum of<br>Remains</div>
  <div class="label" style="left:806px;top:3020px">Trustee's Certificate</div>
  <div class="label c" style="left:451px;top:3116px">Durable Power of Attorney<br>with Nomination of Guardian</div>
  <div class="label r" style="right:812px;top:3020px">Health Care Proxy</div>
  <div class="label r" style="right:911px;top:2902px">Revocable Living Trust</div>
  <div class="label r" style="right:961px;top:2740px">Irrevocable Living<br>Trust</div>
  <div class="label r" style="right:923px;top:2586px">Quitclaim Deed</div>
  <div class="label r" style="right:812px;top:2476px">Trust Amendments</div>
</section>

<section class="faq">
  <h2 class="faq-title">FAQ</h2>
  <div class="rule" style="left:66px;top:3410px;width:56px"></div>
  <div class="faq-item open" style="top:3462px">
    <div class="q"><span class="num">01</span><span>What will a divorce cost me?</span><em class="tog">−</em></div>
    <p class="a">I currently bill my family law clients at <b>$385.00 per hour</b>. Although I will make every effort to keep costs reasonable for you and work within the agreed upon retainer, I cannot give you a fixed price for a divorce (or any other family law matter). The reason is because I cannot predict what the opposition will file during the litigation process, or what pleadings I may need to file on your behalf in order to achieve your goals in this matter.</p>
  </div>
  <div class="faq-item" style="top:3664px;padding-bottom:18px">
    <div class="q"><span class="num">02</span><span>How long will it take for me to get divorced?</span><em class="tog">+</em></div>
  </div>
  <div class="faq-item" style="top:3726px;padding-bottom:18px">
    <div class="q"><span class="num">03</span><span>What kinds of information should I bring with me for my free 30-minute<br>consultation?</span><em class="tog">+</em></div>
  </div>
  <div class="abs" style="left:917px;top:3320px;width:256px;height:480px;border:2px solid var(--green);border-left:none"></div>
  <div class="abs" style="left:917px;top:3320px;width:2px;height:30px;background:var(--green)"></div>
  <div class="abs" style="left:917px;top:3775px;width:2px;height:25px;background:var(--green)"></div>
  <div class="abs" style="left:783px;top:3350px;width:353px;height:425px;background:linear-gradient(160deg,#e9e2d4 0%,#2c3a55 30%,#1e2a40 70%,#d9d3c5 100%)" role="img" aria-label="Two law reference binders on wills and evidence"></div>
</section>

<section class="contact">
  <div class="abs" style="left:36px;top:3983px;width:256px;height:527px;border:2px solid var(--green)"></div>
  <div class="abs" style="left:68px;top:4000px;width:429px;height:465px;background:linear-gradient(180deg,#bcd1e6 0%,#d8d6cf 40%,#c9b59a 70%,#7a3a2a 90%)" role="img" aria-label="Street view of the two-storey office building with a flowering tree"></div>
  <h2 class="contact-title">CONTACT</h2>
  <div class="field" style="left:568px;top:4167px;width:252px;height:46px">Your Name</div>
  <div class="field" style="left:835px;top:4167px;width:252px;height:46px">Phone Number</div>
  <div class="field" style="left:568px;top:4225px;width:519px;height:46px">Email Address</div>
  <div class="field" style="left:568px;top:4285px;width:519px;height:86px">Message</div>
  <a class="btn solid" href="#">SUBMIT <span class="dot"><svg width="12" height="12" viewBox="0 0 12 12"><path d="M2 6h8M7 3l3 3-3 3" stroke="#fff" stroke-width="1.6" fill="none"/></svg></span></a>
</section>

<footer class="site-footer">
  <div class="foot-h" style="left:232px">QUICK LINKS</div>
  <ul class="foot-links"><li>About</li><li>Family Law</li><li>Estate Planning</li><li>Location</li><li>Contact</li></ul>
  <div class="foot-brand">Dolores Quintana<br>Attorney at Law</div>
  <div class="foot-h" style="left:834px">CONTACT US</div>
  <div class="foot-contact">
    <div class="row"><span class="ic"><svg width="12" height="12" viewBox="0 0 24 24"><path d="M6 3h3l2 5-2 1.5c1 2.5 3 4.5 5.5 5.5L16 13l5 2v3c0 1.5-1.5 3-3 3C10 21 3 14 3 6c0-1.5 1.5-3 3-3z" fill="#2f8a1f"/></svg></span><span>CALL US : 978-555-0142<br>FAX US : 978-555-0143</span></div>
    <div class="row"><span class="ic"><svg width="12" height="10" viewBox="0 0 12 10"><rect x="0.5" y="0.5" width="11" height="9" fill="none" stroke="#2f8a1f"/><path d="M1 1l5 4 5-4" fill="none" stroke="#2f8a1f"/></svg></span><span>EMAIL US<br>info@doloresquintanalaw.com</span></div>
    <div class="row"><span class="ic"><svg width="10" height="14" viewBox="0 0 10 14"><path d="M5 13S1 8 1 5a4 4 0 018 0c0 3-4 8-4 8z" fill="#2f8a1f"/><circle cx="5" cy="5" r="1.5" fill="#fff"/></svg></span><span>74 Harbor Lane<br>Beverly, MA 01915</span></div>
  </div>
  <div class="foot-rule"></div>
  <div class="copy">Copyright © 2025 All Rights Reserved By Company name</div>
</footer>

</body>
</html>
```